Thornvale Group needs a business card design

We need a new business card design using the logo recently selected in a logo competition on Pixel Bazaar. Our business is a consultancy specializing in aviation and energy and the winning business card design will promote an image of precision and professionalism with creativity.

Please use the logo with the name on the front of the card and use a complementary font. Make the back white with either the light grey or dark grey logo.

Target Market(s)

Senior finance and legal leaders at aviation and energy companies

Industry/Entity Type

Management Consulting

Contact Information for Business Card

Peter Castrell
President
Thornvale Group

www.thornvalegroup.example

(555) 204-6391
pc@thornvalegroup.example

Requirements
Must have
• Professional font that goes well with the logo font

```html
<!DOCTYPE html>
<html lang="en">
<head>
<meta charset="utf-8">
<title>Thornvale Group — Business Card</title>
<link rel="stylesheet" href="https://fonts.googleapis.com/css2?family=Arimo:wght@400;700&display=swap">
<style>
  :root {
    --backdrop: #5a514b;
    --card: #1c1d1f;
    --card-edge: #141517;
    --brand-blue: #1f4f8c;
    --text-light: #e9e9ea;
    --text-muted: #6c6d70;
    --divider: #8a8b8e;
    --back-mark: #c9cacc;
  }
  * { margin: 0; padding: 0; box-sizing: border-box; }
  html, body { width: 1200px; height: 787px; overflow: hidden; }
  body {
    background: var(--backdrop);
    font-family: "Arimo", Arial, sans-serif;
    position: relative;
  }
  .card {
    position: absolute;
    width: 520px;
    height: 297px;
    background: var(--card);
    border: 1px solid var(--card-edge);
    box-shadow: 0 10px 24px rgba(0,0,0,0.35);
  }
  /* Back of card */
  .card-back { left: 70px; top: 120px; }
  .card-back .brand-name {
    position: absolute;
    left: 0; right: 0; top: 110px;
    text-align: center;
    font-size: 34px;
    font-weight: 700;
    color: var(--back-mark);
  }
  .card-back .web {
    position: absolute;
    left: 0; right: 0; top: 200px;
    text-align: center;
    font-size: 14px;
    letter-spacing: 3px;
    color: var(--text-light);
  }
  /* Front of card */
  .card-front { left: 610px; top: 370px; }
  .card-front .brand-name {
    position: absolute;
    left: 24px; width: 210px; top: 128px;
    text-align: center;
    font-size: 26px;
    font-weight: 700;
    color: var(--brand-blue);
  }
  .card-front .divider {
    position: absolute;
    left: 254px; top: 28px;
    width: 1px; height: 241px;
    background: linear-gradient(to bottom, transparent, var(--divider) 30%, var(--divider) 70%, transparent);
  }
  .details {
    position: absolute;
    left: 276px; top: 42px;
    right: 18px;
    color: var(--text-light);
    font-size: 14px;
    line-height: 19px;
  }
  .details .person {
    font-size: 17px;
    font-weight: 700;
    color: var(--brand-blue);
    line-height: 20px;
  }
  .details .role {
    color: var(--text-muted);
    font-size: 14px;
    margin-bottom: 16px;
  }
  .contact {
    list-style: none;
    margin-top: 10px;
  }
  .contact li {
    display: flex;
    align-items: center;
    gap: 6px;
  }
  .contact svg { width: 12px; height: 12px; flex: none; }
</style>
</head>
<body>
  <section class="card card-back" aria-label="Card back">
    <div class="brand-name">Thornvale Group</div>
    <div class="web">www.thornvalegroup.example</div>
  </section>

  <section class="card card-front" aria-label="Card front">
    <div class="brand-name">Thornvale Group</div>
    <div class="divider"></div>
    <div class="details">
      <div class="person">Peter J. Castrell</div>
      <div class="role">President</div>
      <div>Thornvale Group LLC</div>
      <div>Finance and Strategy Consulting</div>
      <div>Aviation - Manufacturing - Energy</div>
      <ul class="contact">
        <li>
          <svg viewBox="0 0 12 12" aria-hidden="true"><path fill="#1f4f8c" d="M2 1h2.5l1 3-1.5 1a6 6 0 0 0 3 3l1-1.5 3 1V11c-5 0-9-4-9-9z"/></svg>
          (555) 204-6391
        </li>
        <li>
          <svg viewBox="0 0 12 12" aria-hidden="true"><rect x="1" y="2.5" width="10" height="7" fill="#1f4f8c"/><path d="M1 2.5l5 4 5-4" stroke="#1c1d1f" fill="none"/></svg>
          pc@thornvalegroup.example
        </li>
        <li>
          <svg viewBox="0 0 12 12" aria-hidden="true"><circle cx="6" cy="6" r="5" fill="#1f4f8c"/><path d="M1 6h10M6 1c-2 3-2 7 0 10M6 1c2 3 2 7 0 10" stroke="#1c1d1f" stroke-width="0.8" fill="none"/></svg>
          thornvalegroup.example
        </li>
      </ul>
    </div>
  </section>
</body>
</html>
```